Professional & attention grabbing.

A business card design, front and back. I already have a logo I will attach, but I am open to something new as well.
Things to include:
Name:
Title:
Phone:
Email:
Wanting something that is professional but attention grabbing.
Also we do a lot of work using drones on natural gas pipelines (leading the future)if you want to include any of that. I'm open to ideas.
Target Market(s)
Natural gas transmission industry / greenhouse gas mitigation industry
Industry/Entity Type
Business
Colors
Designer to choose colors to be used in the design.
Look and feel
Each slider illustrates characteristics of the customer's brand and the style your logo design should communicate.

```html
<!DOCTYPE html>
<html lang="en">
<head>
<meta charset="utf-8">
<title>Veldra Pipeline Inspections — Business Card</title>
<link rel="stylesheet" href="https://fonts.googleapis.com/css2?family=Roboto:wght@300;400;700&display=swap">
<style>
  :root {
    --bg: #e9e7e3;
    --charcoal: #2f2f31;
    --charcoal-light: #3b3b3d;
    --red: #c41f26;
    --red-dark: #a3181e;
    --white: #ffffff;
    --grey: #6d6e70;
    --text-light: #f1f1f1;
  }
  * { box-sizing: border-box; margin: 0; padding: 0; }
  html, body { width: 1200px; height: 950px; overflow: hidden; }
  body {
    background: var(--bg);
    font-family: "Roboto", Arial, sans-serif;
    position: relative;
  }
  .card {
    position: absolute;
    left: 250px;
    width: 700px;
    height: 400px;
    border-radius: 20px;
    overflow: hidden;
    box-shadow: 0 6px 18px rgba(0,0,0,0.18);
  }
  .card-front { top: 50px; background: var(--white); }
  .card-back { top: 500px; background: var(--red); }

  .front-shape { position: absolute; inset: 0; width: 100%; height: 100%; }

  .brand {
    position: absolute;
    display: flex;
    align-items: center;
    gap: 14px;
  }
  .brand-mark { width: 34px; height: 34px; }
  .brand-name {
    font-weight: 700;
    font-size: 30px;
    line-height: 1.05;
    letter-spacing: 0.5px;
  }
  .card-front .brand { left: 48px; top: 178px; }
  .card-front .brand-mark { background: var(--red); }
  .card-front .brand-name { color: var(--charcoal); }

  .contact {
    position: absolute;
    right: 44px;
    top: 70px;
    text-align: right;
    color: var(--text-light);
  }
  .contact-name {
    color: var(--red);
    font-size: 30px;
    font-weight: 400;
    letter-spacing: 1px;
    text-transform: uppercase;
  }
  .contact-title {
    font-size: 21px;
    font-weight: 300;
    margin: 6px 0 22px;
    letter-spacing: 0.5px;
  }
  .contact-list { list-style: none; }
  .contact-item {
    display: flex;
    justify-content: flex-end;
    align-items: center;
    gap: 12px;
    font-size: 19px;
    font-weight: 300;
    margin-bottom: 12px;
  }
  .contact-icon { width: 16px; height: 16px; fill: var(--red); flex: none; }

  .card-back .brand { right: 70px; bottom: 60px; }
  .card-back .brand-mark { background: var(--white); width: 60px; height: 60px; }
  .card-back .brand-name { color: var(--white); font-size: 24px; }
  .back-web {
    position: absolute;
    left: 48px;
    bottom: 40px;
    color: var(--white);
    font-size: 17px;
    font-weight: 300;
    font-style: normal;
    transform-origin: left bottom;
    transform: rotate(-90deg) translateY(100%);
    white-space: nowrap;
    letter-spacing: 0.5px;
  }
</style>
</head>
<body>

<section class="card card-front" aria-label="Card front">
  <svg class="front-shape" viewBox="0 0 700 400" preserveAspectRatio="none" aria-hidden="true">
    <path d="M300 0 C 380 0, 400 120, 420 200 C 440 290, 470 370, 560 400 L700 400 L700 0 Z" fill="var(--charcoal)"/>
    <path d="M290 0 C 360 10, 375 120, 395 200 C 415 290, 445 370, 520 400 L560 400 C 470 370, 440 290, 420 200 C 400 120, 380 0, 300 0 Z" fill="var(--red)"/>
    <path d="M284 0 C 354 10, 369 120, 389 200 C 409 290, 439 370, 512 400 L520 400 C 445 370, 415 290, 395 200 C 375 120, 360 10, 290 0 Z" fill="var(--red-dark)"/>
  </svg>

  <div class="brand">
    <span class="brand-mark" aria-hidden="true"></span>
    <span class="brand-name">VELDRA<br>INSPECTIONS</span>
  </div>

  <div class="contact">
    <h1 class="contact-name">Dana Mercer</h1>
    <p class="contact-title">CEO/FOUNDER</p>
    <ul class="contact-list">
      <li class="contact-item">555 014 2290
        <svg class="contact-icon" viewBox="0 0 16 16" aria-hidden="true"><path d="M3.5 1.5l2.5 0 1 3.5-1.8 1.3c.8 1.7 2 2.9 3.7 3.7L10.2 8.2l3.3 1v2.5c0 .9-.8 1.6-1.7 1.5C6.6 12.6 3 9 2.6 3.5 2.5 2.4 2.7 1.5 3.5 1.5z"/></svg>
      </li>
      <li class="contact-item">dana@veldrainspect.com
        <svg class="contact-icon" viewBox="0 0 16 16" aria-hidden="true"><path d="M1 3h14v10H1z M1 3l7 6 7-6" /></svg>
      </li>
      <li class="contact-item">www.veldrainspect.com
        <svg class="contact-icon" viewBox="0 0 16 16" aria-hidden="true"><circle cx="8" cy="8" r="7"/></svg>
      </li>
    </ul>
  </div>
</section>

<section class="card card-back" aria-label="Card back">
  <address class="back-web">www.veldrainspect.com</address>
  <div class="brand">
    <span class="brand-mark" aria-hidden="true"></span>
    <span class="brand-name">VELDRA</span>
  </div>
</section>

</body>
</html>
```